Norvane Website Design (New Start Up Investment Management Firm)

We need a website designed. We have attached a Powerpoint with our proposed website content (which is quite minimal), the format is just a suggestion but we would like to see your alternative and improved ideas. We are a boutique investment firm so are looking for something sleek and professional. I have included on the last page of the attachment our brand colours and font styles as well as attaching our logo design. We would like the successful designer to design the website and build the buttons etc.

On the "Contact Us" page, we are open to suggestions on how best to show the map, whether is should be static or open a google maps page. We would like the phone number and email address to be set up so people can click on them on their phone and it calls us or emails us directly.

We would prefer not to have photos of landscapes on the site.
Our website is hosted on a Linux based website.

We would also like 3 links at the bottom of each page for links to pdfs:
- Disclaimer, Terms and Conditions of Web Site Use
- Stewardship
- Pillar III

Target Market(s)

Institutional Investors

Industry/Entity Type

Investment

Coding

Coded - Design and coding required

Number of Pages Required

3 page

Font styles to use
Other font styles liked:
• Logo: Lato, Text: Source Sans Pro

Colors

Designer to choose colors to be used in the design.

Requirements
Must have
• The website must use the colours and fonts on the last page of the attached powerpoint. I can't see an option to select the exact colour palette below so please look at the PPT.
• For others please see Project description.
Should not have
• Landscape photos

```html
<!DOCTYPE html>
<html lang="en">
<head>
<meta charset="utf-8">
<title>Norvane Investment Management – About Us</title>
<link rel="stylesheet" href="https://fonts.googleapis.com/css2?family=Lato:wght@300;400;700&display=swap">
<style>
  :root {
    --navy: #0b2e64;
    --accent: #4a8fd4;
    --body-grey: #6a6d72;
    --white: #ffffff;
    --sky-top: #eef2f7;
    --sky-mid: #dfe7f0;
    --sky-low: #c9d6e4;
  }
  * { box-sizing: border-box; margin: 0; padding: 0; }
  html, body { width: 1200px; height: 755px; overflow: hidden; }
  body { font-family: "Lato", sans-serif; position: relative; background: var(--sky-top); }

  .hero-backdrop {
    position: absolute; left: 0; top: 0; width: 1200px; height: 632px;
    background:
      radial-gradient(ellipse 520px 300px at 600px 330px, rgba(248,249,251,0.95), rgba(248,249,251,0) 100%),
      linear-gradient(160deg, var(--sky-low) 0%, var(--sky-top) 35%, var(--sky-mid) 70%, var(--sky-low) 100%);
  }

  .site-header { position: absolute; left: 0; top: 0; width: 1200px; height: 110px; }
  .brand { position: absolute; left: 120px; top: 30px; display: flex; align-items: center; gap: 14px; }
  .brand-mark { width: 58px; height: 58px; background: var(--navy); }
  .brand-name { font-size: 46px; font-weight: 400; color: var(--navy); letter-spacing: 1px; line-height: 1; }

  .main-nav { position: absolute; top: 47px; left: 617px; display: flex; gap: 0; }
  .main-nav a {
    font-size: 16.5px; font-weight: 400; color: var(--navy); text-decoration: none;
    position: absolute; white-space: nowrap;
  }
  .main-nav .current { color: var(--accent); }

  .about { position: absolute; left: 0; top: 196px; width: 1200px; text-align: center; }
  .about-title { font-size: 40px; font-weight: 400; color: var(--accent); letter-spacing: 0.5px; line-height: 1.2; }
  .about-lead { margin: 22px auto 0; width: 880px; font-size: 20px; line-height: 29px; color: var(--navy); font-weight: 400; }
  .about-body { margin: 16px auto 0; width: 880px; font-size: 16px; line-height: 23px; color: var(--body-grey); font-weight: 400; }

  .site-footer { position: absolute; left: 0; top: 632px; width: 1200px; height: 123px; background: var(--navy); color: var(--white); }
  .footer-links { position: absolute; left: 123px; top: 28px; font-size: 16.5px; display: flex; gap: 12px; }
  .footer-links a { color: var(--white); text-decoration: none; }
  .footer-links .sep { opacity: 0.9; }
  .copyright { position: absolute; left: 123px; top: 64px; font-size: 13px; font-weight: 300; }
  .social { position: absolute; left: 886px; top: 32px; }
</style>
</head>
<body>
  <div class="hero-backdrop" role="img" aria-label="Soft blue-grey view looking up at glass office towers"></div>

  <header class="site-header">
    <div class="brand">
      <span class="brand-mark"></span>
      <span class="brand-name">NORVANE</span>
    </div>
    <nav class="main-nav">
      <a href="#" style="left:0">HOME</a>
      <a href="#" class="current" style="left:93px">ABOUT US</a>
      <a href="#" style="left:218px">APPROACH</a>
      <a href="#" style="left:351px">CONTACT US</a>
    </nav>
  </header>

  <main class="about">
    <h1 class="about-title">ABOUT US</h1>
    <p class="about-lead">Norvane Investment Management was founded in 2016 with a clear vision to create an independent and nimble firm focused on generating superior risk-adjusted returns.</p>
    <p class="about-body">Norvane has designed an innovative investment approach which aims to harness the best elements of alternative investment management whilst reducing its recognised shortcomings. We are a performance and client focused firm, committed to building lasting relationships, treating our clients like partners rather than revenue streams.</p>
  </main>

  <footer class="site-footer">
    <div class="footer-links">
      <a href="#">Disclaimer</a><span class="sep">|</span>
      <a href="#">Terms and Conditions</a><span class="sep">|</span>
      <a href="#">Stewardship</a><span class="sep">|</span>
      <a href="#">Pillar III</a>
    </div>
    <p class="copyright">© 2017 Company Name&nbsp; All right reserved&nbsp; Term of Use</p>
    <svg class="social" width="200" height="38" viewBox="0 0 200 38" aria-label="Social links">
      <g fill="none" stroke="#ffffff" stroke-width="1.5">
        <circle cx="18" cy="19" r="17"/>
        <circle cx="59" cy="19" r="17"/>
        <circle cx="99" cy="19" r="17"/>
        <circle cx="140" cy="19" r="17"/>
        <circle cx="180" cy="19" r="17"/>
      </g>
    </svg>
  </footer>
</body>
</html>
```